BRAMBLE is looking for a design partner

We are a group of videographers, photographers and editors currently rebranding our company. Originally Marcus Kelloway Photography, we have grown over the years into a company that does a lot of different things for a variety of corporate clients. It's clear the company is no longer Marcus, but a whole team. We have submitted a design contest for our new logo, purchased our new URL/email, and are now looking to get things moving on the website. We have most copy ready and are looking to help move online. The site should load quickly, be mobile friendly, look modern, and be very easy to navigate. Our videos run on Vimeo so we need to make sure that we can embed or run videos from the Vimeo account.

We are excited to be starting this new chapter. Hopefully you can come along with us! Marcus

Target Market(s)

Businesses looking to see what we do, examples of our work, and who we are.

Industry/Entity Type

Multimedia

Font styles to use
Serif
Sans Serif

Colors
33a6d7
3176b5
ffffff

Requirements
Must have
• I believe we are looking for a bright white background website.

Here is a list of areas that we will need to have on the site.
-Overview video near top
-Our Mission
-Details of services
-About the team
-Our History (3 sections: Different from Start, Growth, Transformation)
-Working at BRAMBLE (area for talent and freelancer to see employment info, current opening, how to apply
-Internship Program details
-Contact Form
-FAQ
Nice to have
• Social media links, slideshow, etc
We need photo and videos sprinkled throughout the site to give it as modern a look as possible. I am open to using this for backgrounds or to segment sections. See our current site here marcuskellowayphotography.com/business/
Should not have
• Cannot load slow. This is our current challenge. Any thing we can do to move this along will be helpful.

```html
<!DOCTYPE html>
<html lang="en">
<head>
<meta charset="utf-8">
<title>Bramble — Multimedia Studio</title>
<link href="https://fonts.googleapis.com/css2?family=Roboto+Condensed:wght@400;700&family=Montserrat:wght@400;500&display=swap" rel="stylesheet">
<style>
:root{
  --sky:#33a6d7;
  --royal:#3176b5;
  --white:#ffffff;
  --ink:#222831;
  --muted:#9a9a9a;
  --mist:#eeeeee;
  --line:#d4d4d4;
}
*{box-sizing:border-box;margin:0;padding:0}
html,body{width:1200px;height:4819px;overflow:hidden;background:var(--white)}
body{font-family:"Roboto Condensed",Arial,sans-serif;color:var(--ink);position:relative}
section,header,footer{position:absolute;left:0;width:1200px}
.abs{position:absolute}
.btn{position:absolute;display:flex;align-items:center;justify-content:center;gap:8px;border-radius:30px;background:var(--sky);color:var(--white);font-size:17px;text-transform:uppercase}
.btn svg{width:16px;height:16px}
h2{font-weight:700;text-transform:uppercase;color:var(--royal);letter-spacing:-.5px}

/* header */
.site-header{top:0;height:88px;border-top:3px solid var(--sky);background:var(--white)}
.brand{left:150px;top:18px;display:flex;align-items:center;gap:14px;font-size:44px;font-weight:700;color:var(--royal)}
.brand i{width:44px;height:44px;border-radius:50%;background:var(--royal);display:block}
.nav{left:486px;top:33px;display:flex;gap:20px;font-size:16px;text-transform:uppercase}
.nav a{color:var(--ink);text-decoration:none;position:relative}
.nav a.active::after{content:"";position:absolute;left:0;right:0;top:51px;height:3px;background:var(--sky)}
.search{left:1038px;top:34px}

/* hero */
.hero{top:88px;height:629px;background:linear-gradient(120deg,#4a5566 0%,#2e3a4c 45%,#57616f 100%)}
.hero h1{left:206px;top:150px;font-size:96px;color:var(--white);font-weight:700;letter-spacing:-1px}
.hero p{left:208px;top:296px;width:460px;font-size:21px;color:var(--white);line-height:31px}
.arrow{width:48px;height:48px;border-radius:50%;background:#1c1f24;display:flex;align-items:center;justify-content:center;top:290px}
.dots{left:558px;top:565px;display:flex;gap:8px}
.dots span{width:12px;height:12px;border-radius:50%;background:var(--white)}
.dots span:nth-child(2){margin-right:18px}

/* what is */
.about{top:717px;height:513px}
.about .photo{left:0;top:0;width:595px;height:513px;background:linear-gradient(180deg,#8fc4ea 0%,#5f9a6a 55%,#3f5e3c 100%)}
.about .panel{left:595px;top:0;width:605px;height:513px;background:var(--royal)}
.about .tag{left:568px;top:80px;width:407px;height:79px;background:var(--white);display:flex;align-items:center;justify-content:center}
.about .tag h2{font-size:46px}
.about p{left:646px;top:205px;width:420px;font-size:14.5px;line-height:31px;color:var(--white)}

/* mission */
.mission{top:1230px;height:614px}
.mission h2{left:144px;top:82px;font-size:48px}
.mission p{left:144px;top:150px;width:470px;font-size:14px;line-height:31px;color:var(--muted)}
.mission .photo{left:730px;top:80px;width:337px;height:534px;background:linear-gradient(180deg,#e9ebee,#b9bec6 60%,#3a3d42)}

/* history */
.history{top:1844px;height:741px;background:var(--sky);color:var(--white);text-align:center}
.history h2{color:var(--white);width:100%;top:95px;font-size:48px;position:absolute}
.history .lead{width:100%;top:173px;font-size:16px}
.card{top:266px;width:290px;height:370px;background:var(--white);border-radius:50px 0 50px 50px;color:var(--ink);padding:34px 22px 0}
.card.mid{background:linear-gradient(180deg,#3a86cc,#2a62a6);color:var(--white);border-radius:50px 50px 0 0}
.card .icon{width:78px;height:78px;display:block;margin:0 auto}
.card h3{font-size:20px;margin:16px 0 12px}
.card p{font-size:12px;line-height:24px;color:var(--muted);height:120px;overflow:hidden}
.card.mid p{color:var(--white)}
.card .more{margin-top:22px;font-size:14px;font-weight:700;text-transform:uppercase;color:var(--royal);display:flex;justify-content:center;align-items:center;gap:6px}
.card .more svg{width:14px;height:14px}
.card.mid .more{color:var(--white)}

/* working */
.working{top:2585px;height:725px;text-align:center}
.working h2{position:absolute;width:100%;top:100px;font-size:48px}
.working .lead{left:250px;width:700px;top:190px;font-size:13.5px;line-height:32px;color:var(--muted)}
.perk{top:346px;width:240px;text-align:center}
.perk .ring{width:102px;height:102px;margin:0 auto;border:3px solid var(--sky);border-radius:50%;display:flex;align-items:center;justify-content:center}
.perk .ring svg{width:46px;height:46px}
.perk h3{margin-top:26px;font-size:25px}

/* contact */
.contact{top:3310px;height:659px;background:var(--mist)}
.contact .photo{left:0;top:3px;width:539px;height:656px;background:linear-gradient(160deg,#6e7e95,#3c4b63 50%,#8a5a48)}
.contact .card-form{left:492px;top:106px;width:562px;height:446px;background:var(--white);box-shadow:0 6px 24px rgba(0,0,0,.08)}
.contact h2{left:40px;top:44px;font-size:46px;position:absolute}
.field{position:absolute;border:1px solid var(--line);font-size:11px;color:#666;padding:10px 14px;background:var(--white)}

/* faq */
.faq{top:3969px;height:490px}
.faq h2{position:absolute;width:100%;text-align:center;top:100px;font-size:48px}
.q{height:52px;border-radius:26px;background:var(--white);box-shadow:0 4px 16px rgba(0,0,0,.09);font-family:Montserrat,Arial,sans-serif;font-size:14px;display:flex;align-items:center;padding-left:26px}
.q b{position:absolute;right:10px;top:9px;width:34px;height:34px;border-radius:50%;background:var(--sky);color:var(--white);font-weight:500;font-size:22px;display:flex;align-items:center;justify-content:center}
.answer{left:193px;top:290px;width:360px;font-family:Montserrat,Arial,sans-serif;font-size:10.5px;line-height:20px;color:var(--muted)}

/* footer */
.site-footer{top:4459px;height:360px;background:var(--royal);color:var(--white)}
.site-footer h4{position:absolute;top:70px;font-size:13px;text-transform:uppercase}
.site-footer .small{font-size:11.5px;line-height:19.5px}
.menu li{list-style:none}
.menu li::before{content:"» ";margin-right:6px}
.social div{display:flex;align-items:center;gap:14px;height:40px}
.social i{width:26px;height:26px;border-radius:50%;background:#1d4f86;display:block}
.copy{position:absolute;width:100%;text-align:center;top:317px;font-size:11px}
</style>
</head>
<body>

<header class="site-header">
  <div class="abs brand"><i></i>Bramble</div>
  <nav class="abs nav">
    <a class="active">Home</a><a>Services</a><a>Portfolio</a><a>Clients</a><a>About</a><a>Contact</a><a>FAQ</a>
  </nav>
  <svg class="abs search" width="16" height="16" viewBox="0 0 16 16"><circle cx="6.5" cy="6.5" r="5" fill="none" stroke="#3176b5" stroke-width="2.4"/><path d="M10 10l4.5 4.5" stroke="#3176b5" stroke-width="2.6" stroke-linecap="round"/></svg>
</header>

<section class="hero" role="img" aria-label="Overview video still: crowd of smiling business guests applauding at an event">
  <h1 class="abs">BRAMBLE</h1>
  <p class="abs">Sed ut perspiciatis unde omnis iste natusoluptatem accusantium doloremque laudantium</p>
  <div class="btn" style="left:208px;top:402px;width:181px;height:51px">Get Started <svg viewBox="0 0 16 16"><circle cx="8" cy="8" r="8" fill="#fff"/><path d="M6.5 4.5L10 8l-3.5 3.5" stroke="#33a6d7" stroke-width="2" fill="none"/></svg></div>
  <div class="abs arrow" style="left:47px"><svg width="14" height="14" viewBox="0 0 14 14"><path d="M9 2L4 7l5 5" stroke="#fff" stroke-width="2" fill="none"/></svg></div>
  <div class="abs arrow" style="left:1114px"><svg width="14" height="14" viewBox="0 0 14 14"><path d="M5 2l5 5-5 5" stroke="#fff" stroke-width="2" fill="none"/></svg></div>
  <div class="abs dots"><span></span><span></span><span></span><span></span></div>
</section>

<section class="about">
  <div class="abs photo" role="img" aria-label="Family of three posing outdoors in front of pine trees and mountains"></div>
  <div class="abs panel"></div>
  <div class="abs tag"><h2>What is Bramble</h2></div>
  <p class="abs">BRAMBLE is about empowering your innate talent. We give our community of artists a platform to do good, to earn a living wage, and to make an impact. This collective allows our clients to work with some of the most talented people in the world to help elevate their message, connect in new ways, and grow. We are content architects, engineers, and artists. BRAMBLE is not just for meeting today's challenge. We are your partner for success.</p>
</section>

<section class="mission">
  <h2 class="abs">Our Mission</h2>
  <p class="abs">Many business and organizations are overwhelmed and struggle to deliver high quality content that speaks to their brand, connects with their customers, and produces results. Our TEAM helps our clients identify their story. We then guide and create beautiful content to communicate their story in variety of video formats. + A reputation for award winning content. With over 1000 videos produced in the last five years clients have complete confidence we deliver. The proof is in our product. High quality award winning storytelling and content. It's who we are.We listen. You may not know how to tell your story.. but you know your brand, your goals, your assets, what makes your company awesome.</p>
  <div class="btn" style="left:144px;top:475px;width:182px;height:53px">Read More <svg viewBox="0 0 16 16"><circle cx="8" cy="8" r="8" fill="#fff"/><path d="M6.5 4.5L10 8l-3.5 3.5" stroke="#33a6d7" stroke-width="2" fill="none"/></svg></div>
  <div class="abs photo" role="img" aria-label="Videographer kneeling behind a professional camera on a tripod"></div>
</section>

<section class="history">
  <h2>Our History</h2>
  <p class="abs lead">BRAMBLE is the product of more than a decade of forward thinking, evolution, transformation.</p>
  <div class="abs card" style="left:144px">
    <svg class="icon" viewBox="0 0 78 78" fill="none" stroke="#3176b5" stroke-width="2"><rect x="8" y="28" width="62" height="36"/><path d="M8 28l4-14 58 0-4 14M18 14l-4 14M30 14l-4 14M42 14l-4 14M54 14l-4 14M20 64v8M58 64v8M16 40h46"/></svg>
    <h3>Different from the start</h3>
    <p>We got our start in 2008 by Marcus Kelloway who envisioned turning a photography hobby into a small business. Bramble serviced portrait, wedding, and an occasional corporate client. The company distinguished</p>
    <div class="more">Read More <svg viewBox="0 0 16 16"><circle cx="8" cy="8" r="8" fill="#3176b5"/><path d="M6.5 4.5L10 8l-3.5 3.5" stroke="#fff" stroke-width="2" fill="none"/></svg></div>
  </div>
  <div class="abs card mid" style="left:455px">
    <svg class="icon" viewBox="0 0 78 78" fill="none" stroke="#fff" stroke-width="2"><path d="M10 12h10M10 18h10M10 24h6M8 66h64M14 66V54h8v12M28 66V46h8v20M42 66V38h8v28M56 66V26h8v40M16 46l40-32M48 12h10v10"/></svg>
    <h3>Growth</h3>
    <p>Within a few years the company evolved into video work. This may have been inevitable given Marcus's vast experience in broadcast television and Lumen award winning storyteller.</p>
    <div class="more">Read More <svg viewBox="0 0 16 16"><circle cx="8" cy="8" r="8" fill="#fff"/><path d="M6.5 4.5L10 8l-3.5 3.5" stroke="#3176b5" stroke-width="2" fill="none"/></svg></div>
  </div>
  <div class="abs card" style="left:766px">
    <svg class="icon" viewBox="0 0 78 78" fill="none" stroke="#3176b5" stroke-width="2"><circle cx="22" cy="20" r="10"/><path d="M12 20h20M22 10v20"/><rect x="44" y="10" width="22" height="16"/><ellipse cx="24" cy="46" rx="12" ry="5"/><path d="M12 46v16c0 3 5 5 12 5s12-2 12-5V46M12 54c0 3 5 5 12 5s12-2 12-5"/><circle cx="56" cy="50" r="6"/><path d="M46 68c0-6 4-10 10-10s10 4 10 10M32 20h12M54 26v18"/></svg>
    <h3>Transformation</h3>
    <p>To meet increasing demand, many of our talented freelancers became employees. Eventually it became clear the company was truly no longer Marcus.We still did photography but 80% of our work was video production.</p>
    <div class="more">Read More <svg viewBox="0 0 16 16"><circle cx="8" cy="8" r="8" fill="#3176b5"/><path d="M6.5 4.5L10 8l-3.5 3.5" stroke="#fff" stroke-width="2" fill="none"/></svg></div>
  </div>
</section>

<section class="working">
  <h2>Working at Bramble</h2>
  <p class="abs lead">Our team is made up of some of the greatest people on earth... who happen to be talented too. We are strong believers that our people are the difference between mundane and awesome content. If you are committed to learning, supporting, and helping those around you we want to hear from you.</p>
  <div class="abs perk" style="left:95px"><div class="ring"><svg viewBox="0 0 46 46"><circle cx="23" cy="23" r="18" fill="none" stroke="#3176b5" stroke-width="5"/><path d="M23 13v11h-7" stroke="#3176b5" stroke-width="4" fill="none"/></svg></div><h3>Full time jobs</h3></div>
  <div class="abs perk" style="left:350px"><div class="ring"><svg viewBox="0 0 46 46" fill="none" stroke="#3176b5" stroke-width="3.5"><rect x="6" y="10" width="34" height="30" rx="2"/><path d="M6 20h34M14 5v10M32 5v10"/></svg></div><h3>*Based on availability</h3></div>
  <div class="abs perk" style="left:631px"><div class="ring"><svg viewBox="0 0 46 46" fill="#3176b5"><circle cx="23" cy="14" r="6"/><circle cx="11" cy="18" r="5"/><circle cx="35" cy="18" r="5"/><path d="M12 36c0-7 5-12 11-12s11 5 11 12zM2 34c0-6 4-10 9-10 2 0 3 0 4 1-3 3-4 6-4 9zM44 34c0-6-4-10-9-10-2 0-3 0-4 1 3 3 4 6 4 9z"/></svg></div><h3>Freelance partners</h3></div>
  <div class="abs perk" style="left:867px"><div class="ring"><svg viewBox="0 0 46 46" fill="#3176b5"><path d="M4 8h38v24H4zM8 12v16h30V12z"/><path d="M17 34h12v4h5v3H12v-3h5z"/></svg></div><h3>How to apply</h3></div>
  <div class="btn" style="left:509px;top:575px;width:182px;height:53px">Read More <svg viewBox="0 0 16 16"><circle cx="8" cy="8" r="8" fill="#fff"/><path d="M6.5 4.5L10 8l-3.5 3.5" stroke="#33a6d7" stroke-width="2" fill="none"/></svg></div>
</section>

<section class="contact">
  <div class="abs photo" role="img" aria-label="Team of crew members cheering in front of an outdoor festival stage"></div>
  <div class="abs card-form">
    <h2>Contact Form</h2>
    <div class="field" style="left:42px;top:128px;width:234px;height:37px">First Name</div>
    <div class="field" style="left:287px;top:128px;width:234px;height:37px">Last Name</div>
    <div class="field" style="left:42px;top:178px;width:234px;height:38px">E mail id</div>
    <div class="field" style="left:287px;top:178px;width:234px;height:38px">Ph. No.</div>
    <div class="field" style="left:42px;top:229px;width:479px;height:99px">Message</div>
    <div class="btn" style="left:42px;top:352px;width:136px;height:43px">Submit <svg viewBox="0 0 16 16"><circle cx="8" cy="8" r="8" fill="#fff"/><path d="M6.5 4.5L10 8l-3.5 3.5" stroke="#33a6d7" stroke-width="2" fill="none"/></svg></div>
  </div>
</section>

<section class="faq">
  <h2>Frequently Asked Questions</h2>
  <div class="abs q" style="left:167px;top:215px;width:408px">How to Download Your Photos<b>−</b></div>
  <p class="abs answer">Lorem ipsum dolor sit amet, consectetur adipiscing elit, sed do eiusmod tempor incididunt ut labor</p>
  <div class="abs q" style="left:167px;top:339px;width:408px">Order Prints<b>+</b></div>
  <div class="abs q" style="left:621px;top:215px;width:410px">Need help finding my photos<b>+</b></div>
  <div class="abs q" style="left:621px;top:277px;width:410px">Need help finding my video<b>+</b></div>
  <div class="abs q" style="left:621px;top:339px;width:410px">Using the MKP APP for your photos<b>+</b></div>
</section>

<footer class="site-footer">
  <h4 style="left:144px">Signup Newsletter</h4>
  <div class="abs small" style="left:144px;top:122px;width:227px;height:32px;background:#fff;color:#444;padding:6px 20px">Enter Email</div>
  <div class="abs small" style="left:144px;top:161px;width:101px;height:34px;background:var(--sky);display:flex;align-items:center;justify-content:center;font-weight:700">SIGN UP</div>

  <h4 style="left:446px">Contact Us</h4>
  <div class="abs small" style="left:446px;top:102px;width:230px">
    <div style="display:flex;gap:14px"><span>⦿</span><span>4120 Alder Row, Suite 12,<br>Portvale, FL 33901</span></div>
    <div style="display:flex;gap:14px;margin-top:12px"><span>✆</span><span>Phone : 555.014.2290</span></div>
    <div style="display:flex;gap:14px;margin-top:16px"><span>✉</span><span>contact@marcuskellowayphotography.com</span></div>
  </div>

  <h4 style="left:753px">Menu</h4>
  <ul class="abs small menu" style="left:753px;top:104px">
    <li>Home</li><li>Services</li><li>Portfolio</li><li>Clients</li><li>About</li><li>Contact</li><li>FAQ</li>
  </ul>

  <h4 style="left:936px">Connect With Us</h4>
  <div class="abs small social" style="left:936px;top:100px">
    <div><i></i>Newsroom</div><div><i></i>Updates</div><div><i></i>Careers</div>
  </div>

  <p class="copy">Copyrights @ 2020 Bramble. All Rights Reserved &nbsp;|&nbsp; Privacy Policy &nbsp;|&nbsp; Terms and Use</p>
</footer>

</body>
</html>
```